Dental Implant Logo and Business Card for Local Dentist

Design a unique business card and a logo that incorporates a dental implant as a primary focal point or a part of the text. New logo design & business card needs to incorporate our businesses old star shaped logo (attached) and a dental implant, along with our business name. Star logo does not have to remain the exact same colors and can be any size. Looking for a warm, friendly (non-aggressive) design that uses colors in the blue-green palate, partial to mint-turquoise color similar to the images attached . SIMPLE IS GOOD, but looking for creativity to bring all the elements together. OK to incorporate a splash of color. I have attached a few images of implant logos I like along with our existing star shaped logo. *I have also uploaded some images that represent local landscapes & images for the back of the business card. I would like to include a silhouette or sketch that represents one one of these areas on the back of the business card to convey the connection to our community and local roots of our business since we are 4th generation members of this community . Can visit our dental practice website for more info. www.hartwellandodegarddentalcare.example Card Must Haves on Front of Card:1. business name "Hartwell & Odegard Dental Care" 2. My Name: "Colin Odegard D.D.S."3. Phone # (925) 754-6020Other info for card (can be front or back)Address: 7840 Quarry Ridge Rd. #2C Larkfield, Ca 94531e-mail: millerandsimarrodentalcare@gmail.comcosmetic, family, & impDesign a unique business card and a logo that incorporates a dental implant as a primary focal point or a part of the text. New logo design & business card needs to incorporate our businesses old star shaped logo (attached) and a dental implant, along with our business name. Star logo does not have to remain the exact same colors and can be any size. Looking for a warm, friendly (non-aggressive) design that uses colors in the blue-green palate, partial to mint-turquoise color similar to the images attached . SIMPLE IS GOOD, but looking for creativity to bring all the elements together. OK to incorporate a splash of color. I have attached a few images of implant logos I like along with our existing star shaped logo. *I have also uploaded some images that represent local landscapes & images for the back of the business card. I would like to include a silhouette or sketch that represents one one of these areas on the back of the business card to convey the connection to our community and local roots of our business since we are 4th generation members of this community . Can visit our dental practice website for more info. www.hartwellandodegarddentalcare.example Card Must Haves on Front of Card:1. business name "Hartwell & Odegard Dental Care" 2. My Name: "Colin Odegard D.D.S."3. Phone # (925) 754-6020Other info for card (can be front or back)Address: 7840 Quarry Ridge Rd. #2C Larkfield, Ca 94531e-mail: millerandsimarrodentalcare@gmail.comcosmetic, family, & implant dentistry

Target Market(s)

Families

Industry/Entity Type

Dental

Contact Information for Business Card

See Project description above

Logo Text

Hartwell & Odegard Dental Care

Font styles to use
Serif

Colors
ffffff
33b8a4
87cfc6
0492cd
33a6d7
0255a3

Requirements
Must have
• *See Description...
• Card Must Haves on Front of Card:
• 1. business name "Hartwell & Odegard Dental Care"
• 2. My Name: "Colin Odegard D.D.S."
• 3. Phone # (555) 318-4297
• Other info for card (can be front or back)
• Address: 7840 Quarry Ridge Rd. #2C Larkfield, Ca 90217
• e-mail: hartwellandodegarddentalcare@example-mail.com
Nice to have
• Local image sketch or silhouette on back side of business card with remaining information on back: address, website, e-mail etc.

```html
<!DOCTYPE html>
<html lang="en">
<head>
<meta charset="utf-8">
<title>Hartwell &amp; Odegard Dental Care – Business Card</title>
<link href="https://fonts.googleapis.com/css2?family=Noto+Serif:wght@400;700&family=Dosis:wght@500;600;700&display=swap" rel="stylesheet">
<style>
  :root {
    --bg: #ecebe8;
    --card: #ffffff;
    --brand-blue: #1f5fae;
    --teal: #33b8a4;
    --ink: #1d1d1f;
    --band: #7a876c;
    --sky-top: #c9d6de;
    --sky-low: #dfe5e6;
    --hill: #c9b38a;
    --water: #7f9fc4;
    --icon-blue: #2f5fae;
  }
  * { box-sizing: border-box; margin: 0; padding: 0; }
  html, body { width: 1200px; height: 1200px; overflow: hidden; }
  body { background: var(--bg); position: relative; font-family: "Dosis", sans-serif; }

  .card {
    position: absolute; left: 180px; width: 840px; height: 480px;
    border-radius: 4px; overflow: hidden;
    box-shadow: 0 6px 18px rgba(0,0,0,.15);
  }

  /* Back */
  .card--back { top: 60px; }
  .back-scene {
    position: absolute; inset: 0;
    background: linear-gradient(180deg,
      var(--sky-top) 0%, var(--sky-low) 40%,
      var(--hill) 58%, #b8a577 66%,
      var(--water) 70%, #6f90b8 100%);
  }
  .back-band {
    position: absolute; left: 0; right: 0; top: 175px; height: 140px;
    background: var(--band);
    display: flex; flex-direction: column; justify-content: center; align-items: center;
    color: #fff;
  }
  .back-name { font-family: "Noto Serif", serif; font-weight: 400; font-size: 46px; white-space: nowrap; }
  .back-tagline {
    font-family: "Noto Serif", serif; font-size: 15px;
    letter-spacing: 9px; text-transform: uppercase; margin-top: 6px; white-space: nowrap;
  }

  /* Front */
  .card--front { top: 660px; background: var(--card); }
  .front-logo {
    position: absolute; left: 60px; top: 80px;
    display: flex; align-items: center; gap: 22px;
  }
  .logo-dot { width: 58px; height: 58px; border-radius: 50%; background: var(--teal); flex: none; }
  .logo-name {
    font-family: "Noto Serif", serif; font-weight: 700; font-size: 40px;
    color: var(--brand-blue); white-space: nowrap;
  }
  .front-tagline {
    position: absolute; left: 140px; top: 140px;
    font-family: "Noto Serif", serif; font-size: 15px; color: var(--teal);
    letter-spacing: 13.5px; text-transform: uppercase; white-space: nowrap;
  }
  .divider { position: absolute; left: 60px; right: 60px; top: 352px; height: 2px; background: var(--teal); }

  .contact { position: absolute; left: 60px; font-size: 19px; color: var(--ink); font-weight: 500; display: flex; align-items: center; gap: 12px; white-space: nowrap; }
  .contact svg { width: 16px; height: 16px; flex: none; }
  .contact--phone { top: 318px; font-style: italic; }
  .contact--email { top: 364px; }
  .contact--web { top: 392px; }

  .person { position: absolute; right: 60px; text-align: right; white-space: nowrap; }
  .person-name { top: 286px; font-size: 28px; font-weight: 700; color: var(--ink); }
  .person-role { top: 322px; font-size: 19px; font-weight: 600; color: var(--brand-blue); }
  .address { top: 368px; font-size: 20px; font-weight: 600; color: var(--ink); line-height: 1.3; }
</style>
</head>
<body>

<section class="card card--back">
  <div class="back-scene" role="img" aria-label="Photo of local landscape: golden hills with wind turbines beside a river under a pale sky"></div>
  <div class="back-band">
    <div class="back-name">Hartwell &amp; Odegard Dental Care</div>
    <div class="back-tagline">Cosmetic &amp; General Dentistry</div>
  </div>
</section>

<section class="card card--front">
  <div class="front-logo">
    <span class="logo-dot"></span>
    <span class="logo-name">Hartwell &amp; Odegard Dental Care</span>
  </div>
  <div class="front-tagline">Cosmetics &amp; General Dentistry</div>

  <div class="contact contact--phone">
    <svg viewBox="0 0 16 16"><path d="M3 1l3 3-2 2c1 2 3 4 5 5l2-2 3 3-2 3C6 14 2 10 1 3z" fill="var(--icon-blue)"/></svg>
    +(555) - 318-4297
  </div>
  <div class="divider"></div>
  <div class="contact contact--email">
    <svg viewBox="0 0 16 16"><rect x="1" y="3" width="14" height="10" fill="var(--icon-blue)"/><path d="M1 3l7 6 7-6" stroke="#fff" stroke-width="1.3" fill="none"/></svg>
    hartwellandodegarddentalcare@example-mail.com
  </div>
  <div class="contact contact--web">
    <svg viewBox="0 0 16 16"><circle cx="8" cy="8" r="6.5" fill="none" stroke="var(--icon-blue)" stroke-width="1.3"/><path d="M1.5 8h13M8 1.5c-3 3-3 10 0 13M8 1.5c3 3 3 10 0 13" stroke="var(--icon-blue)" fill="none"/></svg>
    www.hartwellandodegarddentalcare.example
  </div>

  <div class="person person-name">Colin Odegard D.D.S</div>
  <div class="person person-role">manager</div>
  <div class="person address">7840 Quarry Ridge Rd<br>#2C Larkfield, Ca 90217</div>
</section>

</body>
</html>
```